Simple and Clean business card design

We would like the design to be simple clean and to incorporate our colors.

We are open to your design and talent, we have the dots in our logo as we think of it as data points and we connect data points for people.

We are open to see the great creative and clean design you bring to the table

Contact Information for Business Card

please include: name, position, email, phone and website

Font styles to use
Sans Serif

Requirements
Must have
• my colors incorporated, simplicity
Nice to have
• lots of white space, simplicity
Should not have
• complexicity/ complex art

```html
<!DOCTYPE html>
<html lang="en">
<head>
<meta charset="utf-8">
<title>Nectra — Business Card</title>
<link rel="stylesheet" href="https://fonts.googleapis.com/css2?family=Work+Sans:wght@400;500;600&display=swap">
<style>
  :root {
    --blue: #5a7fbf;
    --green: #34a852;
    --yellow: #f5bb1a;
    --ink: #111111;
    --paper: #ffffff;
    --card-black: #000000;
    --backdrop: #ece6dc;
  }
  * { box-sizing: border-box; margin: 0; padding: 0; }
  html, body {
    width: 1200px; height: 900px; overflow: hidden;
    background: var(--backdrop);
    font-family: "Work Sans", sans-serif;
  }
  .card {
    position: absolute;
    left: 261px;
    width: 656px; height: 357px;
    border-radius: 18px;
    overflow: hidden;
  }
  .card--front { top: 69px; background: var(--paper); }
  .card--back {
    top: 472px; background: var(--card-black);
    display: flex; align-items: center; justify-content: center;
  }

  .color-bands { position: absolute; left: 0; top: 0; width: 100%; }
  .band { display: block; width: 100%; }
  .band--blue { height: 52px; background: var(--blue); }
  .band--green { height: 8px; background: var(--green); margin-top: 4px; }
  .band--yellow { height: 4px; width: 62%; background: var(--yellow); margin-top: 4px; }

  .brand {
    display: flex; align-items: flex-start; gap: 8px;
    font-weight: 600; line-height: 1; letter-spacing: -1px;
  }
  .brand--front { position: absolute; left: 36px; top: 92px; font-size: 80px; color: var(--ink); }
  .brand--back { font-size: 112px; color: var(--paper); margin-top: -10px; }
  .brand-dot { flex: none; border-radius: 50%; background: var(--green); }
  .brand--front .brand-dot { width: 16px; height: 16px; margin-top: 8px; }
  .brand--back .brand-dot { width: 22px; height: 22px; margin-top: 12px; }

  .person { position: absolute; right: 36px; top: 190px; text-align: right; }
  .person-name {
    color: var(--blue); font-weight: 500; font-size: 27px;
    letter-spacing: 2px; line-height: 1;
  }
  .person-role { color: var(--ink); font-size: 17px; margin-top: 6px; line-height: 1; letter-spacing: 0.6px; }
  .accent-bar {
    position: absolute; left: 645px; top: 193px;
    width: 11px; height: 39px; background: var(--blue);
  }
  .divider {
    position: absolute; left: 38px; top: 247px;
    width: 583px; height: 1px; background: var(--blue);
  }

  .contact {
    position: absolute; left: 38px; top: 269px;
    list-style: none; font-size: 17px; color: var(--ink);
    letter-spacing: 0.6px;
  }
  .contact li { display: flex; align-items: center; height: 21.5px; }
  .contact svg { width: 11px; height: 11px; margin-right: 6px; flex: none; }

  .address {
    position: absolute; right: 35px; top: 290px;
    text-align: right; font-style: normal;
    font-size: 17px; line-height: 21.5px; color: var(--ink);
    letter-spacing: 0.6px;
  }
</style>
</head>
<body>

<section class="card card--front" aria-label="Business card front">
  <div class="color-bands" aria-hidden="true">
    <span class="band band--blue"></span>
    <span class="band band--green"></span>
    <span class="band band--yellow"></span>
  </div>

  <div class="brand brand--front"><span>Nectra</span><span class="brand-dot"></span></div>

  <div class="person">
    <p class="person-name">DANIEL REYES</p>
    <p class="person-role">Founder</p>
  </div>
  <span class="accent-bar"></span>
  <span class="divider"></span>

  <ul class="contact">
    <li>
      <svg viewBox="0 0 12 12" aria-hidden="true"><path fill="none" stroke="var(--blue)" stroke-width="1.4" d="M3,1 L4.5,3.5 L3.5,5 C4.2,7 5,8 7,8.8 L8.5,7.6 L11,9.2 L9.6,11 C5,10.5 1.5,7 1,2.4 Z"/></svg>
      <span>0412 585 903</span>
    </li>
    <li>
      <svg viewBox="0 0 12 12" aria-hidden="true"><rect x="1" y="2.5" width="10" height="7" fill="none" stroke="var(--blue)" stroke-width="1.2"/><path d="M1,2.5 L6,6.5 L11,2.5" fill="none" stroke="var(--blue)" stroke-width="1.2"/></svg>
      <span>hello@nectradata.com</span>
    </li>
    <li>
      <svg viewBox="0 0 12 12" aria-hidden="true"><g fill="none" stroke="var(--blue)" stroke-width="1"><circle cx="6" cy="6" r="5"/><ellipse cx="6" cy="6" rx="2.2" ry="5"/><path d="M1,6 H11 M2,3.5 H10 M2,8.5 H10"/></g></svg>
      <span>www.nectradata.com</span>
    </li>
  </ul>

  <address class="address">
    418 Birchwood Lane<br>
    Austin, TX 78701
  </address>
</section>

<section class="card card--back" aria-label="Business card back">
  <div class="brand brand--back"><span>Nectra</span><span class="brand-dot"></span></div>
</section>

</body>
</html>
```